Core values in our company OKV (Residency and Relocation)

Do good:
1. Being Direct and communicative for the benefit of all parties
2. Working for the Benefit of the company, client and team members
3. Wanting to improve to create a better impact
4. Having healthy rivalry
Be ahead of curve:
1. Having the confidence to break through barriers which arise
2. Desire to grow and learn towards establishment and agreed goal
3. Getting off the sidelines and get into the game
4. Keeping the end game in mind having due regard to processes and milestones
5. Self starter and works on own initiative
6. Diligent and impactful in your field of responsibility
Truth and Honesty
2. Have the confidence and ability to speak what you really want to communicate
3. Being truthful to yourself, clients and colleagues to find the innovations that lie within
4. Seeking the truth by opening things up for discussion
5. Being Optimistic
Background Information on our Company:OKV is a professional law firm in London Docklands. We caters for both private and corporate clients ranging from highly regarded and established law firms to boutique and niche immigration practices. We also specialises in expert legal advice and prides itself on providing services that go beyond the expectations of its clients.
What we need: We need a Poster about Truth and Honesty, this is to show one of our values as a company. It will need to be vibrant and straight to the point. Colours can be orange grey white and yellow. Attached is our company logo.
Reason: To remind colleagues that this is one of our main values and it is instilled in our company.
Things we would like:
1. To create a point of focus
2. Use shapes to create visual interest
3. Use creative illustrations
4. Take the viewer’s focus on a journey with clever perspective
Industry/Entity Type
Legal
Requirements
Must have
- a globe (Picture)
- Do good:
- 1. Being Direct and communicative for the benefit of all parties
- 2. Working for the Benefit of the company, client and team members
- 3. Wanting to improve to create a better impact
- 4. Having healthy rivalry
- Be ahead of curve:
- 1. Having the confidence to break through barriers which arise
- 2. Desire to grow and learn towards establishment and agreed goal
- 3. Getting off the sidelines and get into the game
- 4. Keeping the end game in mind having due regard to processes and milestones
- 5. Self starter and works on own initiative
- 6. Diligent and impactful in your field of responsibility
- Truth and Honesty
- 2. Have the confidence and ability to speak what you really want to communicate
- 3. Being truthful to yourself, clients and colleagues to find the innovations that lie within
- 4. Seeking the truth by opening things up for discussion
- 5. Being Optimistic

```html
<!DOCTYPE html>
<html lang="en">
<head>
<meta charset="utf-8">
<title>OKV Core Values Poster</title>
<link rel="stylesheet" href="https://fonts.googleapis.com/css2?family=Tinos:wght@400;700&family=Montserrat:wght@600;700&display=swap">
<style>
  :root{
    --stage:#2b2b2b;
    --paper:#ffffff;
    --mist:#eeeeee;
    --mist-dark:#dcdcdc;
    --ink:#333333;
    --ink-soft:#4a4a4a;
    --orange:#f47c20;
    --amber:#fbb829;
    --chart-red:#c8102e;
    --globe-blue:#3aa0d8;
    --footer:#3a3a3a;
  }
  *{box-sizing:border-box;margin:0;padding:0}
  html,body{width:1200px;height:2163px;overflow:hidden;background:var(--stage)}
  .poster{position:absolute;left:80px;top:346px;width:1040px;height:1470px;background:var(--paper);overflow:hidden;
    font-family:"Montserrat",Arial,sans-serif;color:var(--ink)}
  .hero{position:absolute;left:0;top:0;width:1040px;height:625px;
    background:linear-gradient(180deg,#f7f7f7 0%,#e6e6e6 100%)}
  .hero-frame{position:absolute;left:0;top:0}
  .logo-card{position:absolute;left:0;top:0;width:410px;height:180px;background:#fff;border-bottom-right-radius:40px;
    box-shadow:4px 6px 14px rgba(0,0,0,.18)}
  .logo-name{position:absolute;left:80px;top:28px;font-family:"Tinos",serif;font-weight:700;font-size:78px;line-height:1;color:var(--orange)}
  .logo-tag{position:absolute;left:80px;top:118px;font-family:"Tinos",serif;font-size:20px;color:var(--ink)}
  .chart{position:absolute;left:0;top:0}
  .illustration{position:absolute;left:450px;top:60px;width:560px;height:560px;border-radius:50%;
    background:radial-gradient(circle at 45% 55%,#5cb8e8 0%,var(--globe-blue) 45%,rgba(58,160,216,.15) 70%,rgba(58,160,216,0) 72%)}
  .values{position:absolute;left:0;top:625px;width:1040px;height:845px}
  .values svg{position:absolute;left:0;top:0}
  .title{position:absolute;left:50px;top:70px;font-family:"Tinos",serif;color:var(--ink);line-height:.95}
  .title .the{font-size:48px}
  .title .core{font-size:64px}
  .title .core b{font-weight:700}
  .title .of{font-size:78px;font-weight:700}
  .pill{position:absolute;height:60px;border-radius:0 30px 30px 0;
    background:linear-gradient(90deg,var(--orange),var(--amber));
    font-family:"Tinos",serif;font-weight:700;font-size:25px;color:var(--ink);padding:15px 0 0 30px;
    box-shadow:0 8px 10px -6px rgba(0,0,0,.35)}
  .pill-truth{left:0;top:300px;width:330px}
  .pill-good{left:452px;top:26px;width:330px}
  .pill-ahead{left:452px;top:308px;width:330px}
  .list{position:absolute;list-style:none}
  .list li{position:relative;padding-left:38px;font-size:17px;font-weight:700;line-height:21px;color:var(--ink-soft)}
  .list li svg{position:absolute;left:0;top:2px}
  .list-truth{left:30px;top:395px;width:375px}
  .list-truth li{margin-bottom:26px;text-align:justify}
  .list-good{left:485px;top:112px;width:530px}
  .list-good li{margin-bottom:13px}
  .list-ahead{left:485px;top:395px;width:530px}
  .list-ahead li{margin-bottom:16px}
  .footer{position:absolute;left:0;top:725px;width:1040px;height:120px}
  .site{position:absolute;left:535px;top:24px;font-family:"Tinos",serif;font-weight:700;font-size:27px;color:#fff}
  .site-icon{position:absolute;left:490px;top:24px}
  .socials{position:absolute;left:560px;top:70px;display:flex;gap:12px}
  .socials span{width:30px;height:30px;border:2px solid var(--orange);border-radius:50%}
</style>
</head>
<body>
<div class="poster">
  <section class="hero">
    <svg class="chart" width="1040" height="625" viewBox="0 0 1040 625" aria-hidden="true">
      <polyline points="0,417 200,290 320,395 397,296 452,373 640,380 847,384 946,461 1040,395"
        fill="none" stroke="var(--chart-red)" stroke-width="3"/>
      <g fill="var(--chart-red)">
        <circle cx="200" cy="290" r="7"/><circle cx="320" cy="395" r="7"/>
        <circle cx="397" cy="296" r="7"/><circle cx="946" cy="461" r="7"/>
      </g>
    </svg>
    <div class="illustration" role="img" aria-label="Illustration of a businessman with a briefcase inspecting a blue globe through a magnifying glass"></div>
    <svg class="hero-frame" width="1040" height="200" viewBox="0 0 1040 200" aria-hidden="true">
      <path d="M1040 4 H440 Q420 4 420 24 V150 Q420 190 380 190 H0" fill="none" stroke="var(--orange)" stroke-width="6"/>
    </svg>
    <div class="logo-card">
      <div class="logo-name">OKV</div>
      <div class="logo-tag">Residency and Relocation</div>
    </div>
  </section>

  <section class="values">
    <svg width="1040" height="845" viewBox="0 0 1040 845" aria-hidden="true">
      <defs>
        <linearGradient id="panelShade" x1="0" y1="0" x2="1" y2="0">
          <stop offset="0" stop-color="#f4f4f4"/><stop offset="1" stop-color="#e2e2e2"/>
        </linearGradient>
      </defs>
      <path d="M0 0 H452 V560 Q452 760 300 845 H0 Z" fill="url(#panelShade)"/>
      <path d="M440 725 H1040 V845 H300 Q400 790 440 725 Z" fill="var(--footer)"/>
    </svg>

    <h1 class="title">
      <div class="the">THE</div>
      <div class="core">Core <b>Value</b></div>
      <div class="of">OF OKV</div>
    </h1>

    <div class="pill pill-truth">Truth and Honesty</div>
    <ul class="list list-truth">
      <li><svg width="16" height="16" viewBox="0 0 16 16"><circle cx="8" cy="8" r="6.5" fill="none" stroke="var(--orange)" stroke-width="1.5"/><path d="M5 8l2 2 4-4" fill="none" stroke="var(--orange)" stroke-width="1.5"/></svg>Having the confidence to break through barriers which arise</li>
      <li><svg width="16" height="16" viewBox="0 0 16 16"><circle cx="8" cy="8" r="6.5" fill="none" stroke="var(--orange)" stroke-width="1.5"/><path d="M5 8l2 2 4-4" fill="none" stroke="var(--orange)" stroke-width="1.5"/></svg>Have the confidence and ability to speak what you really want to communicate</li>
      <li><svg width="16" height="16" viewBox="0 0 16 16"><circle cx="8" cy="8" r="6.5" fill="none" stroke="var(--orange)" stroke-width="1.5"/><path d="M5 8l2 2 4-4" fill="none" stroke="var(--orange)" stroke-width="1.5"/></svg>Being truthful to yourself, clients and colleagues to find the innovations that lie within</li>
      <li><svg width="16" height="16" viewBox="0 0 16 16"><circle cx="8" cy="8" r="6.5" fill="none" stroke="var(--orange)" stroke-width="1.5"/><path d="M5 8l2 2 4-4" fill="none" stroke="var(--orange)" stroke-width="1.5"/></svg>Seeking the truth by opening things up for discussion</li>
      <li><svg width="16" height="16" viewBox="0 0 16 16"><circle cx="8" cy="8" r="6.5" fill="none" stroke="var(--orange)" stroke-width="1.5"/><path d="M5 8l2 2 4-4" fill="none" stroke="var(--orange)" stroke-width="1.5"/></svg>Being Optimistic</li>
    </ul>

    <div class="pill pill-good">Do good:</div>
    <ul class="list list-good">
      <li><svg width="16" height="16" viewBox="0 0 16 16"><circle cx="8" cy="8" r="6.5" fill="none" stroke="var(--orange)" stroke-width="1.5"/><path d="M5 8l2 2 4-4" fill="none" stroke="var(--orange)" stroke-width="1.5"/></svg>Being Direct and communicative for the benefit of all parties</li>
      <li><svg width="16" height="16" viewBox="0 0 16 16"><circle cx="8" cy="8" r="6.5" fill="none" stroke="var(--orange)" stroke-width="1.5"/><path d="M5 8l2 2 4-4" fill="none" stroke="var(--orange)" stroke-width="1.5"/></svg>Working for the Benefit of the company, client and team members</li>
      <li><svg width="16" height="16" viewBox="0 0 16 16"><circle cx="8" cy="8" r="6.5" fill="none" stroke="var(--orange)" stroke-width="1.5"/><path d="M5 8l2 2 4-4" fill="none" stroke="var(--orange)" stroke-width="1.5"/></svg>Wanting to improve to create a better impact</li>
      <li><svg width="16" height="16" viewBox="0 0 16 16"><circle cx="8" cy="8" r="6.5" fill="none" stroke="var(--orange)" stroke-width="1.5"/><path d="M5 8l2 2 4-4" fill="none" stroke="var(--orange)" stroke-width="1.5"/></svg>Having healthy rivalry</li>
    </ul>

    <div class="pill pill-ahead">Be ahead of curve:</div>
    <ul class="list list-ahead">
      <li><svg width="16" height="16" viewBox="0 0 16 16"><circle cx="8" cy="8" r="6.5" fill="none" stroke="var(--orange)" stroke-width="1.5"/><path d="M5 8l2 2 4-4" fill="none" stroke="var(--orange)" stroke-width="1.5"/></svg>Having the confidence to break through barriers which arise</li>
      <li><svg width="16" height="16" viewBox="0 0 16 16"><circle cx="8" cy="8" r="6.5" fill="none" stroke="var(--orange)" stroke-width="1.5"/><path d="M5 8l2 2 4-4" fill="none" stroke="var(--orange)" stroke-width="1.5"/></svg>Desire to grow and learn towards establishment and agreed goal</li>
      <li><svg width="16" height="16" viewBox="0 0 16 16"><circle cx="8" cy="8" r="6.5" fill="none" stroke="var(--orange)" stroke-width="1.5"/><path d="M5 8l2 2 4-4" fill="none" stroke="var(--orange)" stroke-width="1.5"/></svg>Getting off the sidelines and get into the game</li>
      <li><svg width="16" height="16" viewBox="0 0 16 16"><circle cx="8" cy="8" r="6.5" fill="none" stroke="var(--orange)" stroke-width="1.5"/><path d="M5 8l2 2 4-4" fill="none" stroke="var(--orange)" stroke-width="1.5"/></svg>Keeping the end game in mind having due regard to processes and milestones</li>
      <li><svg width="16" height="16" viewBox="0 0 16 16"><circle cx="8" cy="8" r="6.5" fill="none" stroke="var(--orange)" stroke-width="1.5"/><path d="M5 8l2 2 4-4" fill="none" stroke="var(--orange)" stroke-width="1.5"/></svg>Self starter and works on own initiative</li>
      <li><svg width="16" height="16" viewBox="0 0 16 16"><circle cx="8" cy="8" r="6.5" fill="none" stroke="var(--orange)" stroke-width="1.5"/><path d="M5 8l2 2 4-4" fill="none" stroke="var(--orange)" stroke-width="1.5"/></svg>Diligent and impactful in your field of responsibility</li>
    </ul>

    <div class="footer">
      <svg class="site-icon" width="30" height="30" viewBox="0 0 30 30" aria-hidden="true">
        <g fill="none" stroke="var(--orange)" stroke-width="2">
          <circle cx="15" cy="15" r="12"/><ellipse cx="15" cy="15" rx="5" ry="12"/>
          <line x1="3" y1="15" x2="27" y2="15"/><line x1="5" y1="9" x2="25" y2="9"/><line x1="5" y1="21" x2="25" y2="21"/>
        </g>
      </svg>
      <div class="site">www.residencyrelocation.example</div>
      <div class="socials" aria-hidden="true">
        <span></span><span></span><span></span><span></span><span></span><span></span><span></span><span></span><span></span>
      </div>
    </div>
  </section>
</div>
</body>
</html>
```